Baby Organic Coconut Body Lotion

Meadow Hush Naturals is developing a line of Organic and Natural skin care products for babies and toddlers, although our skin care can also be used by adults too. These products include a body lotion, shampoo & body wash, powder, hair cream, massage body oil, bath soak, baby balm, Bar Soap, gift box and many more.
This will be an ever expanding line so the list will go on and on. We are looking forward for an eye catching designs. I attached some of our current label designs and product images. Also, we have different Baby organic body lotion and Baby organic shampoo & body wash with different fruit flavours. Coconut lotion will share the same design with the shampoo & body wash. I would like you to start with the coconut design. I have uploaded plastic bottles with different colourful caps. The bottle with the white cap is for the coconut design. the bottle with the red cap is for the strawberry design. the bottle with the orange cap is for the orange design. the bottle with the yellow cap is for the pineapple design. the bottle with the green cap is for the apple design. Bear in my mind that my baby organic skin care are made with different fruit flavours.
Target Market(s)
My target market are for mothers that wants to buy there baby and toddler skin care products.
Industry/Entity Type
Baby
Look and feel

```html
<!DOCTYPE html>
<html lang="en">
<head>
<meta charset="utf-8">
<title>Skin Care Label Range</title>
<link rel="stylesheet" href="https://fonts.googleapis.com/css2?family=Audiowide&family=Jura:wght@500;600;700&display=swap">
<style>
  :root {
    --canvas-bg: #d6e1e6;
    --band-green: #6ba531;
    --band-text: #f4f8ec;
    --pill-bg: rgba(255, 255, 255, 0.78);
    --pill-text: #cf4fd2;
    --note-text: rgba(70, 70, 70, 0.75);
    --title-text: #ffffff;
  }
  html, body {
    margin: 0;
    padding: 0;
    width: 1200px;
    height: 909px;
    overflow: hidden;
    background: var(--canvas-bg);
  }
  .label-range {
    position: absolute;
    left: 56px;
    top: 274px;
    display: flex;
    gap: 22px;
  }
  .label {
    position: relative;
    width: 200px;
    height: 360px;
    overflow: hidden;
    background: var(--label-bg);
    box-shadow: 0 6px 18px rgba(60, 80, 90, 0.18);
    font-family: "Jura", sans-serif;
  }
  .label--coconut    { --label-bg: #aab0b2; --swoosh: #8f979a; --swoosh-soft: #9ea5a8; --fruit-a: #f1efe8; --fruit-b: #6b4a2e; --title-size: 28px; }
  .label--apple      { --label-bg: #c7e49c; --swoosh: #6cac2c; --swoosh-soft: #9fd062; --fruit-a: #e6f4c8; --fruit-b: #5aa02a; --title-size: 32px; }
  .label--strawberry { --label-bg: #d98d9c; --swoosh: #b5302f; --swoosh-soft: #c95a62; --fruit-a: #e94a4e; --fruit-b: #a61e28; --title-size: 19px; }
  .label--pineapple  { --label-bg: #ebe9a9; --swoosh: #cdbb2b; --swoosh-soft: #dcd36a; --fruit-a: #f7e23a; --fruit-b: #9a8a2c; --title-size: 21px; }
  .label--orange     { --label-bg: #ebba8b; --swoosh: #e07925; --swoosh-soft: #e89a5a; --fruit-a: #fbb23a; --fruit-b: #ef8a12; --title-size: 29px; }

  .label__swoosh {
    position: absolute;
    inset: 0;
    width: 100%;
    height: 100%;
  }
  .label__swoosh .swoosh-soft { fill: var(--swoosh-soft); }
  .label__swoosh .swoosh-main { fill: var(--swoosh); }

  .label__title {
    position: absolute;
    top: 28px;
    left: 14px;
    right: 14px;
    height: 38px;
    margin: 0;
    display: flex;
    align-items: center;
    justify-content: center;
    white-space: nowrap;
    font-family: "Audiowide", sans-serif;
    font-weight: 400;
    font-size: var(--title-size);
    letter-spacing: 0;
    color: var(--title-text);
    line-height: 1;
  }
  .label__subtitle {
    position: absolute;
    top: 74px;
    left: 0;
    right: 0;
    text-align: center;
    font-size: 12px;
    font-weight: 600;
    letter-spacing: 0.5px;
    color: var(--title-text);
    opacity: 0.85;
  }
  .label__band {
    position: absolute;
    top: 100px;
    left: 0;
    right: 0;
    height: 27px;
    background: var(--band-green);
    color: var(--band-text);
    font-size: 15px;
    font-weight: 700;
    line-height: 27px;
    text-align: center;
    white-space: nowrap;
  }
  .label__audience {
    position: absolute;
    top: 138px;
    left: 12px;
    width: 158px;
    height: 28px;
    background: var(--pill-bg);
    display: flex;
    align-items: center;
    gap: 8px;
    padding-left: 10px;
    box-sizing: border-box;
    color: var(--pill-text);
    font-size: 14px;
    font-weight: 700;
    white-space: nowrap;
  }
  .label__audience-icon {
    width: 32px;
    height: 16px;
    border-radius: 8px;
    border: 2px solid var(--pill-text);
    box-sizing: border-box;
    flex: none;
  }
  .label__uses {
    position: absolute;
    top: 172px;
    left: 16px;
    font-size: 8px;
    font-weight: 600;
    color: var(--note-text);
    white-space: nowrap;
  }
  .label__fruit {
    position: absolute;
    left: 0;
    bottom: 0;
    width: 130px;
    height: 100px;
    border-top-right-radius: 60px;
    background: radial-gradient(circle at 35% 55%, var(--fruit-a) 0%, var(--fruit-a) 30%, var(--fruit-b) 100%);
    opacity: 0.95;
  }
</style>
</head>
<body>
<main class="label-range">

  <section class="label label--coconut">
    <svg class="label__swoosh" viewBox="0 0 200 360" preserveAspectRatio="none" aria-hidden="true">
      <path class="swoosh-soft" d="M80 360 Q175 250 182 0 L200 0 L200 360 Z"/>
      <path class="swoosh-main" d="M118 360 Q192 250 200 60 L200 360 Z"/>
    </svg>
    <h2 class="label__title">COCONUT</h2>
    <div class="label__subtitle">SKIN CARE</div>
    <div class="label__band">Organic and Natural</div>
    <div class="label__audience">FOR CHILDREN <span class="label__audience-icon"></span></div>
    <div class="label__uses">Lotion, Shampoo &amp; Body Wash</div>
    <div class="label__fruit" role="img" aria-label="Photo of a halved coconut"></div>
  </section>

  <section class="label label--apple">
    <svg class="label__swoosh" viewBox="0 0 200 360" preserveAspectRatio="none" aria-hidden="true">
      <path class="swoosh-soft" d="M80 360 Q175 250 182 0 L200 0 L200 360 Z"/>
      <path class="swoosh-main" d="M118 360 Q192 250 200 60 L200 360 Z"/>
    </svg>
    <h2 class="label__title">APPLE</h2>
    <div class="label__subtitle">SKIN CARE</div>
    <div class="label__band">Organic and Natural</div>
    <div class="label__audience">FOR CHILDREN <span class="label__audience-icon"></span></div>
    <div class="label__uses">Lotion, Shampoo &amp; Body Wash</div>
    <div class="label__fruit" role="img" aria-label="Photo of green apples, one cut in half"></div>
  </section>

  <section class="label label--strawberry">
    <svg class="label__swoosh" viewBox="0 0 200 360" preserveAspectRatio="none" aria-hidden="true">
      <path class="swoosh-soft" d="M80 360 Q175 250 182 0 L200 0 L200 360 Z"/>
      <path class="swoosh-main" d="M118 360 Q192 250 200 60 L200 360 Z"/>
    </svg>
    <h2 class="label__title">STRAWBERRY</h2>
    <div class="label__subtitle">SKIN CARE</div>
    <div class="label__band">Organic and Natural</div>
    <div class="label__audience">FOR CHILDREN <span class="label__audience-icon"></span></div>
    <div class="label__uses">Lotion, Shampoo &amp; Body Wash</div>
    <div class="label__fruit" role="img" aria-label="Photo of fresh strawberries"></div>
  </section>

  <section class="label label--pineapple">
    <svg class="label__swoosh" viewBox="0 0 200 360" preserveAspectRatio="none" aria-hidden="true">
      <path class="swoosh-soft" d="M80 360 Q175 250 182 0 L200 0 L200 360 Z"/>
      <path class="swoosh-main" d="M118 360 Q192 250 200 60 L200 360 Z"/>
    </svg>
    <h2 class="label__title">PINEAPPLE</h2>
    <div class="label__subtitle">SKIN CARE</div>
    <div class="label__band">Organic and Natural</div>
    <div class="label__audience">FOR CHILDREN <span class="label__audience-icon"></span></div>
    <div class="label__uses">Lotion, Shampoo &amp; Body Wash</div>
    <div class="label__fruit" role="img" aria-label="Photo of a pineapple with sliced pieces"></div>
  </section>

  <section class="label label--orange">
    <svg class="label__swoosh" viewBox="0 0 200 360" preserveAspectRatio="none" aria-hidden="true">
      <path class="swoosh-soft" d="M80 360 Q175 250 182 0 L200 0 L200 360 Z"/>
      <path class="swoosh-main" d="M118 360 Q192 250 200 60 L200 360 Z"/>
    </svg>
    <h2 class="label__title">ORANGE</h2>
    <div class="label__subtitle">SKIN CARE</div>
    <div class="label__band">Organic and Natural</div>
    <div class="label__audience">FOR CHILDREN <span class="label__audience-icon"></span></div>
    <div class="label__uses">Lotion, Shampoo &amp; Body Wash</div>
    <div class="label__fruit" role="img" aria-label="Photo of oranges, one cut in half"></div>
  </section>

</main>
</body>
</html>
```